Icon Design Project

Icon design for mobile site.

Site under development – viewable on pc or mobile at www.go.trellix.net/harborlane

Main site
www.harborlanesupport.co.uk
The branding is to be extended from the main site to the mobile site.

The site is nearly ready. I just need icons and buttons designed. If you visit www.go.trellix.net/harborlane you’ll see that I currently have text links instead of buttons. Looking at the site will help you understand where they go on the site.

Main menu icon set:
- ‘Special Offer’ button (not using Special Offer Image)
- ‘Services’ button
- ‘Contact’ button
- ‘Coffee?’ button
- ‘Video’ button

Category buttons.
These buttons need to integrate images with text. So that the buttons have image+text+border. All images provided with brief. Please go to www.harborlanesupport.co.uk to see how the main site uses them

These buttons should be large – covering nearly the entire width of the mobile page.

Buttons + Text as follows
Special Offer
Online Services
Local Marketing
Organisational Support
Tracking and Reporting
Websites
Mobile Sites
Training Portals
Local Search Optimisation
Call Tracking
SMS Campaigns
QR Campaigns
Mobile Ad Campaigns
Email Marketing
Social Media and Location Marketing
Tracking and Reporting

Please provide final buttons as transparent png/jpg.
Updates

Hi,

Thank you all for getting involved.

Some more detail on what I want.

The top menu: Special Offer - Services - Coffee - Contact, should be the width of the screen. Underneath should be a different looking video button.

Please make the top menu: Special Offer - Services - Coffee? - Contact buttons square with the text under an icon reflecting the buttons function. Graphically they need to stand out so don't feel you have to use the same grey as the menu on the main site (see brief for URL).

The video button can be longer and cover 1/3 to 1/2 the screen. This button should look different to the top menu buttons.

Hope this helps.

Marguerite

Dear all,

Looking forward to seeing your designs. Hope they come in quick so I can give you some feedback.

S

Target Market(s)

Businesses

Industry/Entity Type

Marketing

Requirements
Must have
• Must be in empathy with the design and colours found on site

```html
<!DOCTYPE html>
<html lang="en">
<head>
<meta charset="utf-8">
<title>Special Offer Button</title>
<link rel="stylesheet" href="https://fonts.googleapis.com/css2?family=PT+Sans&display=swap">
<style>
  :root {
    --ink-black: #000000;
    --heart-red: #d40000;
    --label-red: #cc0000;
    --paper-white: #ffffff;
  }
  html, body {
    margin: 0;
    padding: 0;
    width: 1200px;
    height: 1200px;
    overflow: hidden;
    background: var(--paper-white);
  }
  .offer-button {
    position: relative;
    width: 1200px;
    height: 1200px;
  }
  .icon-field {
    position: absolute;
    left: 0;
    top: 0;
    width: 1200px;
    height: 996px;
    background: var(--ink-black);
  }
  .heart-icon {
    display: block;
    width: 1200px;
    height: 996px;
  }
  .heart-icon path {
    fill: var(--heart-red);
  }
  .label-band {
    position: absolute;
    left: 0;
    top: 996px;
    width: 1200px;
    height: 204px;
    background: var(--paper-white);
    display: flex;
    align-items: center;
    justify-content: center;
  }
  .button-label {
    margin: 0;
    font-family: "PT Sans", sans-serif;
    font-weight: 400;
    font-size: 158px;
    line-height: 1;
    color: var(--label-red);
    padding-top: 8px;
  }
</style>
</head>
<body>
  <main class="offer-button">
    <div class="icon-field">
      <svg class="heart-icon" viewBox="0 0 1200 996" aria-hidden="true">
        <path d="M600 996 C 420 780, 30 560, 30 330 C 30 120, 180 5, 330 5 C 460 5, 560 90, 600 180 C 640 90, 740 5, 870 5 C 1020 5, 1170 120, 1170 330 C 1170 560, 780 780, 600 996 Z"/>
      </svg>
    </div>
    <div class="label-band">
      <p class="button-label">Special Offer</p>
    </div>
  </main>
</body>
</html>
```